Verodex business card

Business card for sustainable investment company called "Verodex". Verodex is an exchange platform selling carbon credits between buyers and sellers. Carbon Credits are an environmental commodity for reducing global carbon emissions.

the card should obviously have our logo and the theme should be sustainability/environment mixed with a trading platform.

Contact Information for Business Card

Logo, Name, Title, Phone, Email

Colors
0054AA
0677BA
7BADD7
CADEEF
E8F1F8
0094D4
00A9DD
6FCCEA
C7EBF8
E9F6FB
00AB8E
00BBA5
67D7C9
C6EFE9
E9F9F6
59FF00
82FF00
B8FF75
E3FFCB
F4FFEA

```html
<!DOCTYPE html>
<html lang="en">
<head>
<meta charset="utf-8">
<title>Verodex Business Card</title>
<link href="https://fonts.googleapis.com/css2?family=Raleway:wght@400;600;700&display=swap" rel="stylesheet">
<style>
  :root {
    --backdrop: #e6e8eb;
    --navy: #172b52;
    --navy-mark: #0f1d3a;
    --navy-word: #6f8fc8;
    --ink: #1e2f4d;
    --text: #444a55;
    --accent: #0677ba;
    --accent-light: #0094d4;
    --white: #ffffff;
  }
  * { margin: 0; padding: 0; box-sizing: border-box; }
  html, body { width: 1200px; height: 588px; overflow: hidden; }
  body {
    position: relative;
    background: var(--backdrop);
    font-family: "Raleway", sans-serif;
  }
  .card {
    position: absolute;
    width: 486px;
    height: 287px;
    border-radius: 26px;
  }
  .card--front { left: 87px; top: 141px; background: var(--navy); }
  .card--back { left: 622px; top: 143px; background: var(--white); }

  .brand {
    position: absolute;
    display: flex;
    align-items: center;
    gap: 14px;
  }
  .brand__square { display: block; }
  .brand__name {
    font-weight: 700;
    letter-spacing: 0.5px;
    line-height: 1;
  }
  .card--front .brand { left: 87px; top: 145px; transform: translateY(-50%); }
  .card--front .brand__square { width: 64px; height: 64px; background: var(--navy-mark); }
  .card--front .brand__name { font-size: 40px; color: var(--navy-word); }

  .card--back .brand { left: 114px; top: 77px; transform: translateY(-50%); }
  .card--back .brand__square { width: 52px; height: 52px; background: var(--accent-light); }
  .card--back .brand__name { font-size: 36px; color: var(--ink); }

  .person {
    position: absolute;
    right: calc(486px - 221px);
    top: 202px;
    text-align: right;
  }
  .person__name { font-size: 18px; font-weight: 700; color: var(--ink); letter-spacing: 0.3px; }
  .person__title { font-size: 13px; font-weight: 400; color: var(--text); margin-top: 2px; }

  .divider {
    position: absolute;
    left: 243px;
    top: 186px;
    width: 1px;
    height: 49px;
    background: var(--ink);
  }

  .contact {
    position: absolute;
    left: 260px;
    top: 183px;
    list-style: none;
  }
  .contact__item {
    display: flex;
    align-items: center;
    gap: 6px;
    height: 18.5px;
    font-size: 13px;
    color: var(--text);
  }
  .contact__icon { width: 11px; height: 11px; flex: none; }
</style>
</head>
<body>
  <section class="card card--front">
    <div class="brand">
      <span class="brand__square"></span>
      <span class="brand__name">VERODEX</span>
    </div>
  </section>

  <section class="card card--back">
    <div class="brand">
      <span class="brand__square"></span>
      <span class="brand__name">VERODEX</span>
    </div>

    <div class="person">
      <p class="person__name">MARCUS DELANE</p>
      <p class="person__title">President</p>
    </div>

    <span class="divider"></span>

    <ul class="contact">
      <li class="contact__item">
        <svg class="contact__icon" viewBox="0 0 12 12"><path d="M2.5 1 L4.5 1 L5.3 3.4 L4 4.4 Q5 6.6 7.6 8 L8.6 6.7 L11 7.5 L11 9.5 Q10.5 11 9 11 Q1 10 1 3 Q1 1.5 2.5 1 Z" fill="var(--accent)"/></svg>
        <span>555-310-4827</span>
      </li>
      <li class="contact__item">
        <svg class="contact__icon" viewBox="0 0 12 12"><rect x="1" y="2.5" width="10" height="7" rx="0.8" fill="var(--accent)"/><path d="M1.3 3 L6 6.6 L10.7 3" stroke="var(--white)" stroke-width="0.9" fill="none"/></svg>
        <span>marcus@verodex.com</span>
      </li>
      <li class="contact__item">
        <svg class="contact__icon" viewBox="0 0 12 12"><circle cx="6" cy="6" r="5" fill="var(--accent)"/><ellipse cx="6" cy="6" rx="2.2" ry="5" stroke="var(--white)" stroke-width="0.7" fill="none"/><path d="M1 6 H11" stroke="var(--white)" stroke-width="0.7"/></svg>
        <span>www.verodex.com</span>
      </li>
    </ul>
  </section>
</body>
</html>
```